Agriculture farming Hemp and CBD

The logo is in works with your company now, should be ready in a few days. We have our Domain (kestrelbrookhollow.com) We would like to see incorporated seed to growth, but not necessary. we would like to nature colors and some black and green. we have our farm and will be growing and selling HEMP and CBD we are based in the state of Virginia. Would like to incorporate the words pause, play, rewind if possible but not necessary.

Target Market(s)

20 years old to elderly

Coding

Coded - Design and coding required

Number of Pages Required

3 page

Font styles to use
Serif

Requirements
Must have
• I'm not sure on the must haves, we are open to any ideas, we would definitely like to see Hemp and CBD included, may the life cycle of seed to plant. We must have a pop up asking if you are 20 years old before they can enter our site and to view or purchase our product. I want the design to be totally different than what i uploaded.
Nice to have
• Would like to see natural colors as well as black and green
Should not have
• I want

```html
<!DOCTYPE html>
<html lang="en">
<head>
<meta charset="utf-8">
<title>kestrelbrookhollow.com – Home &amp; Age Verification</title>
<link rel="stylesheet" href="https://fonts.googleapis.com/css2?family=Poppins:wght@400;500;700;800&family=Open+Sans:wght@400;600&display=swap">
<style>
  :root{
    --board:#a9a9a9;
    --black:#0f0f0f;
    --green:#18a11f;
    --green-dark:#117a17;
    --red:#e3141c;
    --white:#ffffff;
    --ink:#1d1d1d;
    --text:#444444;
    --section-grey:#dcdcdc;
    --card-grey:#f4f4f4;
    --photo-deep:#1f3a1c;
    --photo-mid:#4f7a3c;
    --photo-light:#a9c98a;
  }
  *{box-sizing:border-box;margin:0;padding:0}
  html,body{width:969px;height:1200px;overflow:hidden;background:var(--board)}
  .board{position:relative;width:1736px;height:2150px;background:var(--board);transform:scale(0.55818);transform-origin:0 0}
  .page{position:absolute;top:44px;width:806px;height:2064px;background:var(--white);overflow:hidden;font-family:"Open Sans",Arial,sans-serif;color:var(--text)}
  .page--home{left:43px}
  .page--gate{left:892px}
  .abs{position:absolute}

  .header{left:0;top:0;width:806px;height:54px;background:var(--black)}
  .brand{left:96px;top:12px;font-family:"Poppins",sans-serif;font-weight:700;font-size:19px;color:var(--white);letter-spacing:-.2px;line-height:30px}
  .nav{left:409px;top:20px;display:flex;gap:24px;font-size:10px;color:var(--white);letter-spacing:.2px}
  .nav .is-active{color:var(--green)}

  .hero-photo{left:0;top:54px;width:806px;height:400px;background:linear-gradient(180deg,#3b5a2e 0%,#2d4a24 40%,#24411f 100%),var(--photo-deep)}
  .hero-photo::after{content:"";position:absolute;inset:0;background:radial-gradient(ellipse at 50% 55%,rgba(160,175,150,.35),transparent 45%),linear-gradient(90deg,rgba(80,120,55,.5),transparent 35%,transparent 65%,rgba(80,120,55,.5))}
  .hero-title{left:0;top:186px;width:806px;text-align:center;font-family:"Poppins",sans-serif;font-weight:800;font-size:32px;color:var(--white);letter-spacing:.5px}
  .btn{display:inline-block;background:var(--green);color:var(--white);font-size:10.5px;text-align:center;line-height:27px;height:27px}
  .hero-btn{left:360px;top:235px;width:86px;line-height:28px;height:28px}
  .arrow{top:219px;width:30px;height:30px;border-radius:50%;background:var(--white)}
  .arrow svg{position:absolute;left:9px;top:8px}
  .wave{left:0;width:806px}

  .welcome-title{left:96px;top:498px;font-family:"Poppins",sans-serif;font-weight:400;font-size:27px;line-height:33px;color:var(--ink)}
  .rule{height:3px;width:80px;background:var(--green)}
  .welcome-copy{left:96px;top:603px;width:262px;font-size:8.6px;line-height:20.5px}
  .welcome-btn{left:96px;top:736px;width:86px}
  .welcome-shadow{left:432px;top:689px;width:107px;height:91px;background:var(--black)}
  .welcome-photo{left:449px;top:505px;width:260px;height:258px;background:radial-gradient(ellipse at 55% 70%,var(--photo-mid),var(--photo-deep) 45%,#2a3329 70%),#2a3329}
  .welcome-photo::after{content:"";position:absolute;left:0;top:0;width:100%;height:45%;background:linear-gradient(180deg,rgba(200,210,190,.35),transparent)}

  .section-grey{left:0;width:806px;background:var(--section-grey)}
  .section-title{left:0;width:806px;text-align:center;font-family:"Poppins",sans-serif;font-weight:400;font-size:27px;color:var(--ink)}
  .rule--center{left:368px;width:70px}

  .service-card{top:943px;width:199px;height:188px;background:var(--white)}
  .service-card svg{position:absolute;left:13px;top:15px}
  .service-card h3{position:absolute;left:13px;top:68px;font-family:"Poppins",sans-serif;font-weight:400;font-size:13.5px;line-height:18px;color:var(--ink)}
  .service-card p{position:absolute;left:13px;top:92px;width:176px;font-size:6px;line-height:12.5px}
  .btn-outline{display:inline-block;border:1px solid var(--green);color:var(--green);font-size:10px;width:82px;height:23px;line-height:21px;text-align:center}
  .service-card .btn-outline{position:absolute;left:13px;top:143px}

  .media-card{top:1346px;width:197px;height:258px;background:var(--card-grey)}
  .media-photo{position:relative;width:197px;height:118px}
  .media-tag{position:absolute;right:0;bottom:0;width:26px;height:26px;background:rgba(20,20,20,.75)}
  .media-tag svg{position:absolute;left:7px;top:7px}
  .media-card h4{margin:14px 10px 0 13px;font-family:"Poppins",sans-serif;font-weight:400;font-size:10.6px;line-height:16px;letter-spacing:-.1px;color:var(--green)}
  .media-card p{margin:8px 13px 0;font-size:6.2px;line-height:12.8px}
  .media-card .btn-outline{position:absolute;left:14px;top:221px}

  .field{background:var(--white);border:1px solid #e3e3e3;font-size:8.5px;color:#555;padding:8px 9px}
  .submit{left:360px;top:1871px;width:86px;height:28px;line-height:28px}

  .footer{left:0;width:806px;background:var(--black)}
  .footer-links{left:97px;top:2014px;font-size:7.5px;color:#d8d8d8;word-spacing:1px}
  .footer-copy{left:97px;top:2036px;font-size:7.5px;color:#d8d8d8}
  .social{top:2026px;width:10px;height:10px;border-radius:50%;background:#cfcfcf}

  .dim{left:0;top:0;width:806px;height:2064px;background:rgba(0,0,0,.62)}
  .modal{left:260px;top:91px;width:286px;height:242px;background:var(--white);text-align:center}
  .modal h2{position:absolute;left:0;top:24px;width:100%;font-family:"Poppins",sans-serif;font-weight:400;font-size:25.5px;color:var(--ink)}
  .modal .rule{position:absolute;left:103px;top:77px}
  .modal h3{position:absolute;left:0;top:98px;width:100%;font-family:"Poppins",sans-serif;font-weight:400;font-size:16px;color:var(--ink)}
  .modal p{position:absolute;left:36px;top:126px;width:214px;font-size:7px;line-height:15px;color:#333}
  .choice{position:absolute;top:184px;width:54px;height:28px;line-height:28px;color:var(--white);font-family:"Poppins",sans-serif;font-size:15px}
  .choice--yes{left:85px;background:var(--green)}
  .choice--no{left:149px;background:var(--red)}
</style>
</head>
<body>
<div class="board">

  <!-- Home page -->
  <div class="page page--home">
    <div class="abs header"></div>
    <div class="abs brand">kestrelbrookhollow.com</div>
    <nav class="abs nav"><span class="is-active">HOME</span><span>ABOUT US</span><span>SERVICES</span><span>MEDIA</span><span>CONTACT US</span></nav>

    <div class="abs hero-photo" role="img" aria-label="Rows of flowering hemp plants inside a greenhouse"></div>
    <div class="abs hero-title">PAUSE • PLAY • REWIND</div>
    <span class="abs btn hero-btn">READ MORE</span>
    <div class="abs arrow" style="left:36px"><svg width="12" height="14" viewBox="0 0 12 14"><path d="M9 1 L3 7 L9 13" fill="none" stroke="#222" stroke-width="2.4"/></svg></div>
    <div class="abs arrow" style="left:738px"><svg width="12" height="14" viewBox="0 0 12 14"><path d="M3 1 L9 7 L3 13" fill="none" stroke="#222" stroke-width="2.4"/></svg></div>
    <svg class="abs wave" style="top:395px" width="806" height="70" viewBox="0 0 806 70">
      <path d="M0 20 C120 62 240 60 400 22 C560 -8 700 8 806 18 L806 70 L0 70Z" fill="var(--green)"/>
      <path d="M0 30 C110 70 250 68 400 28 C560 2 710 20 806 24 L806 70 L0 70Z" fill="var(--white)"/>
    </svg>

    <h1 class="abs welcome-title">Welcome to<br>kestrelbrookhollow</h1>
    <div class="abs rule" style="left:96px;top:583px"></div>
    <p class="abs welcome-copy">Pellentesque a imperdiet dolor, et auctor est. Fusce sollicitudin lorem et luctus volutpat. Proin placerat dapibus gravida tristique tristique nulla eget hendrerit. Maecenas vel tortor accumsan quam varius imperdiet vel eget elit. Aenean facilisis tincidunt lectus, id dictum nisi luctus eget. Vivamus efficitur ex condimentum, malesuada eros eget, feugiat nibh.</p>
    <span class="abs btn welcome-btn">READ MORE</span>
    <div class="abs welcome-shadow"></div>
    <div class="abs welcome-photo" role="img" aria-label="Close-up of a hemp flower under grow lights"></div>

    <div class="abs section-grey" style="top:834px;height:400px" role="img" aria-label="Soft grey background with a faint leaf pattern"></div>
    <h2 class="abs section-title" style="top:878px">Services</h2>
    <div class="abs rule rule--center" style="top:923px"></div>
    <div class="abs service-card" style="left:97px">
      <svg width="44" height="44" viewBox="0 0 44 44" fill="none" stroke="var(--green)" stroke-width="1.3"><path d="M22 40 V20 M22 22 C14 18 10 10 12 4 C18 8 22 14 22 22 C22 14 26 8 32 4 C34 10 30 18 22 22"/><path d="M22 26 C14 28 8 26 4 20 C12 18 18 20 22 26 C26 20 32 18 40 20 C36 26 30 28 22 26"/></svg>
      <h3>Nulla facilisi</h3>
      <p>Etiam vel massa elementum, bibendum tellus venenatis, feugiat massa. Curabitur venenatis lacinia ornare. Cras sollicitudin cursus dui eu placerat.</p>
      <span class="btn-outline">READ MORE</span>
    </div>
    <div class="abs service-card" style="left:303px">
      <svg width="44" height="44" viewBox="0 0 44 44" fill="none" stroke="var(--green)" stroke-width="1.3"><circle cx="22" cy="22" r="13"/><path d="M24 13 L17 24 H23 L20 32 L28 20 H22Z"/><path d="M22 2 V6 M22 38 V42 M2 22 H6 M38 22 H42 M8 8 L11 11 M33 33 L36 36 M36 8 L33 11 M8 36 L11 33"/></svg>
      <h3>Aliquam erat</h3>
      <p>Etiam vel massa elementum, bibendum tellus venenatis, feugiat massa. Curabitur venenatis lacinia ornare. Cras sollicitudin cursus dui eu placerat.</p>
      <span class="btn-outline">READ MORE</span>
    </div>
    <div class="abs service-card" style="left:509px">
      <svg width="48" height="44" viewBox="0 0 48 44" fill="none" stroke="var(--green)" stroke-width="1.3"><path d="M4 30 H14 L24 34 H36 L44 28 M4 40 H16 L28 42 L44 34 M14 30 V40"/><path d="M18 28 C18 20 30 20 30 28Z"/><path d="M24 20 V10 C24 4 32 2 38 2 C38 8 34 12 28 12 M24 14 C20 12 16 8 16 4 C20 4 24 8 24 12"/></svg>
      <h3>Pellentesque enim</h3>
      <p>Etiam vel massa elementum, bibendum tellus venenatis, feugiat massa. Curabitur venenatis lacinia ornare. Cras sollicitudin cursus dui eu placerat.</p>
      <span class="btn-outline">READ MORE</span>
    </div>
    <svg class="abs wave" style="top:1180px" width="806" height="60" viewBox="0 0 806 60">
      <path d="M0 12 C120 52 240 52 400 16 C560 -10 700 4 806 8 L806 60 L0 60Z" fill="var(--green)"/>
      <path d="M0 20 C110 56 250 58 400 22 C560 -4 710 14 806 14 L806 60 L0 60Z" fill="var(--white)"/>
    </svg>

    <h2 class="abs section-title" style="top:1282px">Media</h2>
    <div class="abs rule rule--center" style="top:1327px;left:363px;width:80px"></div>
    <div class="abs media-card" style="left:97px">
      <div class="media-photo" role="img" aria-label="Open hands holding capsules and a dried hemp bud" style="background:linear-gradient(135deg,#eaeaea,#c9b7a6 55%,#e9e9e9)"><span class="media-tag"><svg width="12" height="12" viewBox="0 0 12 12" fill="none" stroke="#fff" stroke-width="1"><rect x="1" y="2" width="10" height="8"/><path d="M3 5 H9 M3 7 H9"/></svg></span></div>
      <h4>Etiam massa elementum bibendum tellus venenatis.</h4>
      <p>Vivamus lacus justo, ultrices nec erat in, euismod iaculis mauris. Vivamus eleifend vitae nulla vel malesuada. In ac malesuada lacus.</p>
      <span class="btn-outline">READ MORE</span>
    </div>
    <div class="abs media-card" style="left:304px">
      <div class="media-photo" role="img" aria-label="Trays of drying hemp flowers in a processing room" style="background:linear-gradient(180deg,#b9c4c9 0%,#6d8a55 45%,#3f5e2c 100%)"><span class="media-tag"><svg width="12" height="12" viewBox="0 0 12 12" fill="#fff"><path d="M1 4 H4 L10 1 V11 L4 8 H1Z"/></svg></span></div>
      <h4>Cras augue magna, placerat eget nulla non congue suscipit</h4>
      <p>Vivamus lacus justo, ultrices nec erat in, euismod iaculis mauris. Vivamus eleifend vitae nulla vel malesuada. In ac malesuada lacus.</p>
      <span class="btn-outline">READ MORE</span>
    </div>
    <div class="abs media-card" style="left:511px">
      <div class="media-photo" role="img" aria-label="Bright green hemp leaves in warm sunlight" style="background:linear-gradient(135deg,#d9a21e 0%,#6fae2d 40%,#2f7a1c 100%)"><span class="media-tag"><svg width="12" height="12" viewBox="0 0 12 12" fill="none" stroke="#fff" stroke-width="1"><rect x="1" y="2" width="10" height="9"/><path d="M1 5 H11 M4 1 V3 M8 1 V3"/></svg></span></div>
      <h4>Vestibulum ante ipsum primis in faucibus orci luctus</h4>
      <p>Vivamus lacus justo, ultrices nec erat in, euismod iaculis mauris. Vivamus eleifend vitae nulla vel malesuada. In ac malesuada lacus.</p>
      <span class="btn-outline">READ MORE</span>
    </div>

    <div class="abs section-grey" style="top:1658px;height:330px" role="img" aria-label="Soft grey background with a faint leaf pattern"></div>
    <h2 class="abs section-title" style="top:1702px">Contact Us</h2>
    <div class="abs rule rule--center" style="top:1748px;left:363px;width:80px"></div>
    <div class="abs field" style="left:97px;top:1766px;width:302px;height:27px">First Name</div>
    <div class="abs field" style="left:97px;top:1798px;width:302px;height:27px">Email</div>
    <div class="abs field" style="left:97px;top:1831px;width:302px;height:27px">Phone Number</div>
    <div class="abs field" style="left:406px;top:1766px;width:302px;height:92px">Message</div>
    <span class="abs btn submit">SUBMIT</span>
    <svg class="abs wave" style="top:1945px" width="806" height="40" viewBox="0 0 806 40">
      <path d="M0 8 C120 36 240 36 400 10 C560 -8 700 2 806 4 L806 40 L0 40Z" fill="var(--green)"/>
      <path d="M0 16 C110 42 250 42 400 16 C560 -2 710 12 806 10 L806 40 L0 40Z" fill="var(--black)"/>
    </svg>
    <div class="abs footer" style="top:1984px;height:80px"></div>
    <div class="abs footer-links">Home &nbsp;|&nbsp; About Us &nbsp;|&nbsp; Services &nbsp;|&nbsp; Media &nbsp;|&nbsp; Contact Us</div>
    <div class="abs footer-copy">Copyright © 2020 &nbsp; kestrelbrookhollow. &nbsp;All rights reserved.</div>
    <span class="abs social" style="left:668px"></span>
    <span class="abs social" style="left:698px"></span>
  </div>

  <!-- Home page with age gate -->
  <div class="page page--gate">
    <div class="abs header"></div>
    <div class="abs brand">kestrelbrookhollow.com</div>
    <nav class="abs nav"><span class="is-active">HOME</span><span>ABOUT US</span><span>SERVICES</span><span>MEDIA</span><span>CONTACT US</span></nav>

    <div class="abs hero-photo" role="img" aria-label="Rows of flowering hemp plants inside a greenhouse"></div>
    <div class="abs hero-title">PAUSE • PLAY • REWIND</div>
    <span class="abs btn hero-btn">READ MORE</span>
    <div class="abs arrow" style="left:36px"><svg width="12" height="14" viewBox="0 0 12 14"><path d="M9 1 L3 7 L9 13" fill="none" stroke="#222" stroke-width="2.4"/></svg></div>
    <div class="abs arrow" style="left:738px"><svg width="12" height="14" viewBox="0 0 12 14"><path d="M3 1 L9 7 L3 13" fill="none" stroke="#222" stroke-width="2.4"/></svg></div>
    <svg class="abs wave" style="top:395px" width="806" height="70" viewBox="0 0 806 70">
      <path d="M0 20 C120 62 240 60 400 22 C560 -8 700 8 806 18 L806 70 L0 70Z" fill="var(--green)"/>
      <path d="M0 30 C110 70 250 68 400 28 C560 2 710 20 806 24 L806 70 L0 70Z" fill="var(--white)"/>
    </svg>

    <h1 class="abs welcome-title">Welcome to<br>kestrelbrookhollow</h1>
    <div class="abs rule" style="left:96px;top:583px"></div>
    <p class="abs welcome-copy">Pellentesque a imperdiet dolor, et auctor est. Fusce sollicitudin lorem et luctus volutpat. Proin placerat dapibus gravida tristique tristique nulla eget hendrerit. Maecenas vel tortor accumsan quam varius imperdiet vel eget elit. Aenean facilisis tincidunt lectus, id dictum nisi luctus eget. Vivamus efficitur ex condimentum, malesuada eros eget, feugiat nibh.</p>
    <span class="abs btn welcome-btn">READ MORE</span>
    <div class="abs welcome-shadow"></div>
    <div class="abs welcome-photo" role="img" aria-label="Close-up of a hemp flower under grow lights"></div>

    <div class="abs section-grey" style="top:834px;height:400px" role="img" aria-label="Soft grey background with a faint leaf pattern"></div>
    <h2 class="abs section-title" style="top:878px">Services</h2>
    <div class="abs rule rule--center" style="top:923px"></div>
    <div class="abs service-card" style="left:97px">
      <svg width="44" height="44" viewBox="0 0 44 44" fill="none" stroke="var(--green)" stroke-width="1.3"><path d="M22 40 V20 M22 22 C14 18 10 10 12 4 C18 8 22 14 22 22 C22 14 26 8 32 4 C34 10 30 18 22 22"/><path d="M22 26 C14 28 8 26 4 20 C12 18 18 20 22 26 C26 20 32 18 40 20 C36 26 30 28 22 26"/></svg>
      <h3>Nulla facilisi</h3>
      <p>Etiam vel massa elementum, bibendum tellus venenatis, feugiat massa. Curabitur venenatis lacinia ornare. Cras sollicitudin cursus dui eu placerat.</p>
      <span class="btn-outline">READ MORE</span>
    </div>
    <div class="abs service-card" style="left:303px">
      <svg width="44" height="44" viewBox="0 0 44 44" fill="none" stroke="var(--green)" stroke-width="1.3"><circle cx="22" cy="22" r="13"/><path d="M24 13 L17 24 H23 L20 32 L28 20 H22Z"/><path d="M22 2 V6 M22 38 V42 M2 22 H6 M38 22 H42 M8 8 L11 11 M33 33 L36 36 M36 8 L33 11 M8 36 L11 33"/></svg>
      <h3>Aliquam erat</h3>
      <p>Etiam vel massa elementum, bibendum tellus venenatis, feugiat massa. Curabitur venenatis lacinia ornare. Cras sollicitudin cursus dui eu placerat.</p>
      <span class="btn-outline">READ MORE</span>
    </div>
    <div class="abs service-card" style="left:509px">
      <svg width="48" height="44" viewBox="0 0 48 44" fill="none" stroke="var(--green)" stroke-width="1.3"><path d="M4 30 H14 L24 34 H36 L44 28 M4 40 H16 L28 42 L44 34 M14 30 V40"/><path d="M18 28 C18 20 30 20 30 28Z"/><path d="M24 20 V10 C24 4 32 2 38 2 C38 8 34 12 28 12 M24 14 C20 12 16 8 16 4 C20 4 24 8 24 12"/></svg>
      <h3>Pellentesque enim</h3>
      <p>Etiam vel massa elementum, bibendum tellus venenatis, feugiat massa. Curabitur venenatis lacinia ornare. Cras sollicitudin cursus dui eu placerat.</p>
      <span class="btn-outline">READ MORE</span>
    </div>
    <svg class="abs wave" style="top:1180px" width="806" height="60" viewBox="0 0 806 60">
      <path d="M0 12 C120 52 240 52 400 16 C560 -10 700 4 806 8 L806 60 L0 60Z" fill="var(--green)"/>
      <path d="M0 20 C110 56 250 58 400 22 C560 -4 710 14 806 14 L806 60 L0 60Z" fill="var(--white)"/>
    </svg>

    <h2 class="abs section-title" style="top:1282px">Media</h2>
    <div class="abs rule rule--center" style="top:1327px;left:363px;width:80px"></div>
    <div class="abs media-card" style="left:97px">
      <div class="media-photo" role="img" aria-label="Open hands holding capsules and a dried hemp bud" style="background:linear-gradient(135deg,#eaeaea,#c9b7a6 55%,#e9e9e9)"><span class="media-tag"><svg width="12" height="12" viewBox="0 0 12 12" fill="none" stroke="#fff" stroke-width="1"><rect x="1" y="2" width="10" height="8"/><path d="M3 5 H9 M3 7 H9"/></svg></span></div>
      <h4>Etiam massa elementum bibendum tellus venenatis.</h4>
      <p>Vivamus lacus justo, ultrices nec erat in, euismod iaculis mauris. Vivamus eleifend vitae nulla vel malesuada. In ac malesuada lacus.</p>
      <span class="btn-outline">READ MORE</span>
    </div>
    <div class="abs media-card" style="left:304px">
      <div class="media-photo" role="img" aria-label="Trays of drying hemp flowers in a processing room" style="background:linear-gradient(180deg,#b9c4c9 0%,#6d8a55 45%,#3f5e2c 100%)"><span class="media-tag"><svg width="12" height="12" viewBox="0 0 12 12" fill="#fff"><path d="M1 4 H4 L10 1 V11 L4 8 H1Z"/></svg></span></div>
      <h4>Cras augue magna, placerat eget nulla non congue suscipit</h4>
      <p>Vivamus lacus justo, ultrices nec erat in, euismod iaculis mauris. Vivamus eleifend vitae nulla vel malesuada. In ac malesuada lacus.</p>
      <span class="btn-outline">READ MORE</span>
    </div>
    <div class="abs media-card" style="left:511px">
      <div class="media-photo" role="img" aria-label="Bright green hemp leaves in warm sunlight" style="background:linear-gradient(135deg,#d9a21e 0%,#6fae2d 40%,#2f7a1c 100%)"><span class="media-tag"><svg width="12" height="12" viewBox="0 0 12 12" fill="none" stroke="#fff" stroke-width="1"><rect x="1" y="2" width="10" height="9"/><path d="M1 5 H11 M4 1 V3 M8 1 V3"/></svg></span></div>
      <h4>Vestibulum ante ipsum primis in faucibus orci luctus</h4>
      <p>Vivamus lacus justo, ultrices nec erat in, euismod iaculis mauris. Vivamus eleifend vitae nulla vel malesuada. In ac malesuada lacus.</p>
      <span class="btn-outline">READ MORE</span>
    </div>

    <div class="abs section-grey" style="top:1658px;height:330px" role="img" aria-label="Soft grey background with a faint leaf pattern"></div>
    <h2 class="abs section-title" style="top:1702px">Contact Us</h2>
    <div class="abs rule rule--center" style="top:1748px;left:363px;width:80px"></div>
    <div class="abs field" style="left:97px;top:1766px;width:302px;height:27px">First Name</div>
    <div class="abs field" style="left:97px;top:1798px;width:302px;height:27px">Email</div>
    <div class="abs field" style="left:97px;top:1831px;width:302px;height:27px">Phone Number</div>
    <div class="abs field" style="left:406px;top:1766px;width:302px;height:92px">Message</div>
    <span class="abs btn submit">SUBMIT</span>
    <svg class="abs wave" style="top:1945px" width="806" height="40" viewBox="0 0 806 40">
      <path d="M0 8 C120 36 240 36 400 10 C560 -8 700 2 806 4 L806 40 L0 40Z" fill="var(--green)"/>
      <path d="M0 16 C110 42 250 42 400 16 C560 -2 710 12 806 10 L806 40 L0 40Z" fill="var(--black)"/>
    </svg>
    <div class="abs footer" style="top:1984px;height:80px"></div>
    <div class="abs footer-links">Home &nbsp;|&nbsp; About Us &nbsp;|&nbsp; Services &nbsp;|&nbsp; Media &nbsp;|&nbsp; Contact Us</div>
    <div class="abs footer-copy">Copyright © 2020 &nbsp; kestrelbrookhollow. &nbsp;All rights reserved.</div>
    <span class="abs social" style="left:668px"></span>
    <span class="abs social" style="left:698px"></span>

    <div class="abs dim"></div>
    <div class="abs modal" role="dialog" aria-label="Age Verification">
      <h2>Age Verification</h2>
      <div class="rule"></div>
      <h3>Are you 20 years or older?</h3>
      <p>Phasellus nisl est, condimentum vitae faucibus sollicitudin vel metus. Nunc sit amet consequat risus. Curabitur ac elit leo scelerisque elit porttitor.</p>
      <span class="choice choice--yes">YES</span>
      <span class="choice choice--no">NO</span>
    </div>
  </div>

</div>
</body>
</html>
```